Brovick Engineering Core Values Branding Package

Brovick Engineering has recently refined its company Core Values and is seeking a strong, cohesive branding package to visually bring these values to life. The new graphic assets will communicate our commitment to excellence in a way that resonates with our team, clients, and partners in a blue-collar, industrial environment.

We are looking for multiple visual assets with consistent design elements that can be applied across platforms. The tone should reflect strength, reliability, and professionalism while remaining approachable and aligned with our industry.

Core Values & Descriptions
Accountability
“We take ownership of our work and actions, ensuring reliability and trust in every solution we deliver.”

Teamwork
“We collaborate across departments and disciplines to provide the highest level of service and innovation for our clients.”

Integrity
“We operate with honesty, transparency, and ethical standards in all aspects of our business.”

Growth
“We are committed to continuous improvement—of our people, our processes, and our impact in the industry.”

Deliverables

1. Primary Core Values Graphic
A master visual representing all four values together.
Designed for use on posters, office signage, internal presentations.

2. Individual Value Graphics (x4)
One graphic per core value: Accountability, Teamwork, Integrity, Growth.
Cohesive style with slight visual variation to reflect each value’s unique meaning.

Target Market(s)

Employees of Brovick Engineering

Industry/Entity Type

Blue Collar

Font styles to use
Sans Serif

Colors
0054AA
0677BA
7BADD7
CADEEF
E8F1F8
00AB8E
00BBA5
67D7C9
C6EFE9
E9F9F6
EB3D1F
EC4F4E
F09395
F8D3D4
FCEDEE

Requirements
Must have
• Accountability, Teamwork, Integrity, Growth

```html
<!DOCTYPE html>
<html lang="en">
<head>
<meta charset="utf-8">
<title>Brovick Engineering Core Values</title>
<link rel="stylesheet" href="https://fonts.googleapis.com/css2?family=Arimo:wght@400;700&family=Oswald:wght@600&family=Roboto+Condensed:wght@400&display=swap">
<style>
  :root {
    --backdrop: #ececea;
    --paper: #ffffff;
    --navy: #00306a;
    --navy-top: #024a8e;
    --navy-side: #001e42;
    --orange: #f9a11d;
    --orange-top: #fdc02a;
    --orange-side: #f97812;
    --green: #3cb02c;
    --green-top: #55cc3c;
    --green-side: #239021;
    --red: #ce1630;
    --red-top: #e21e45;
    --red-side: #b90f23;
    --heading-grey: #5a5a5a;
    --white: #ffffff;
  }
  html, body {
    margin: 0;
    width: 1200px;
    height: 1146px;
    overflow: hidden;
    background: var(--backdrop);
  }
  .canvas {
    position: relative;
    width: 1200px;
    height: 1146px;
  }
  .poster {
    position: absolute;
    left: 0;
    top: 149px;
    width: 1200px;
    height: 848px;
    display: block;
  }
  .poster-bg { fill: var(--paper); }
  .brand-name { font-family: "Arimo", sans-serif; font-weight: 700; fill: var(--navy); }
  .headline { font-family: "Arimo", sans-serif; font-weight: 700; fill: var(--heading-grey); font-size: 90px; letter-spacing: -1px; }
  .value-title { font-family: "Oswald", sans-serif; font-weight: 600; fill: var(--white); font-size: 40px; text-anchor: middle; }
  .value-text { font-family: "Arimo", sans-serif; font-weight: 400; fill: var(--white); font-size: 23.5px; }
  .divider { stroke: var(--white); stroke-width: 2; }
  .icon { fill: none; stroke: var(--white); stroke-width: 2.6; stroke-linecap: round; stroke-linejoin: round; }
  .contact-text { font-family: "Roboto Condensed", sans-serif; fill: var(--white); font-size: 36px; }
  .contact-icon { fill: none; stroke: var(--green); stroke-width: 2.6; stroke-linecap: round; stroke-linejoin: round; }
  .footer-band { fill: var(--navy); }
  .stairs-art { fill: var(--green); }

  .row-orange .front { fill: var(--orange); }
  .row-orange .top { fill: var(--orange-top); }
  .row-orange .side { fill: var(--orange-side); }
  .row-navy .front { fill: var(--navy); }
  .row-navy .top { fill: var(--navy-top); }
  .row-navy .side { fill: var(--navy-side); }
  .row-green .front { fill: var(--green); }
  .row-green .top { fill: var(--green-top); }
  .row-green .side { fill: var(--green-side); }
  .row-red .front { fill: var(--red); }
  .row-red .top { fill: var(--red-top); }
  .row-red .side { fill: var(--red-side); }
</style>
</head>
<body>
<main class="canvas">
  <svg class="poster" viewBox="0 0 1450 1025" xmlns="http://www.w3.org/2000/svg" aria-label="Brovick Engineering core values poster">
    <defs>
      <g id="value-block">
        <polygon class="front" points="525,185 623,130 1450,130 1450,265 585,265 525,300"/>
        <polygon class="side" points="427,130 525,185 525,300 427,245"/>
        <polygon class="top" points="525,75 623,130 525,185 427,130"/>
      </g>
    </defs>

    <rect class="poster-bg" x="0" y="0" width="1450" height="1025"/>

    <g class="brand">
      <text class="brand-name" x="80" y="215" font-size="66">BROVICK</text>
      <text class="brand-name" x="82" y="262" font-size="33.5">ENGINEERING</text>
    </g>

    <g class="headline-block">
      <text class="headline" x="78" y="410">Core</text>
      <text class="headline" x="78" y="495">Values</text>
    </g>

    <polygon class="stairs-art" role="img" aria-label="Green staircase illustration with a handrail"
             points="0,560 210,760 210,890 225,890 225,910 0,1015 0,715 0,560"/>

    <!-- Accountability -->
    <g class="value-row row-orange">
      <use href="#value-block"/>
      <g class="icon" transform="translate(525,128)">
        <path d="M0,-28 L14,-22 L14,-8 C14,4 6,12 0,16 C-6,12 -14,4 -14,-8 L-14,-22 Z"/>
        <path d="M-7,-7 L-2,-1 L8,-13"/>
        <path d="M-38,22 L-22,14 L-6,18 L14,16 L28,8"/>
        <path d="M-34,30 L-16,28 L16,26"/>
      </g>
      <text class="value-title" x="782" y="212">ACCOUNTABILITY</text>
      <line class="divider" x1="948" y1="155" x2="948" y2="237"/>
      <text class="value-text" x="980" y="174">
        <tspan x="980">We take ownership of our work and</tspan>
        <tspan x="980" dy="25">actions, ensuring reliability and</tspan>
        <tspan x="980" dy="25">trust in every solution we deliver.</tspan>
      </text>
    </g>

    <!-- Teamwork -->
    <g class="value-row row-navy" transform="translate(0,188)">
      <use href="#value-block"/>
      <g class="icon" transform="translate(517,128)">
        <rect x="-22" y="-4" width="18" height="18" rx="2"/>
        <rect x="4" y="-22" width="18" height="18" rx="2"/>
        <path d="M-4,5 L4,-4"/>
        <path d="M-30,26 L-18,16"/>
        <path d="M22,-30 L32,-40"/>
      </g>
      <text class="value-title" x="782" y="212">TEAMWORK</text>
      <line class="divider" x1="948" y1="155" x2="948" y2="237"/>
      <text class="value-text" x="980" y="164">
        <tspan x="980">We collaborate across departments</tspan>
        <tspan x="980" dy="25">and disciplines to provide the highest</tspan>
        <tspan x="980" dy="25">level of service and innovation for</tspan>
        <tspan x="980" dy="25">our clients.</tspan>
      </text>
    </g>

    <!-- Integrity -->
    <g class="value-row row-green" transform="translate(0,376)">
      <use href="#value-block"/>
      <g class="icon" transform="translate(525,132)">
        <circle cx="0" cy="-20" r="11"/>
        <path d="M-5,-20 L-1,-16 L6,-24"/>
        <path d="M-36,-6 L-22,-10 L-14,14 L-28,18 Z"/>
        <path d="M36,-6 L22,-10 L14,14 L28,18 Z"/>
        <path d="M-16,0 L-4,-4 L10,6 L2,14 L-8,8"/>
      </g>
      <text class="value-title" x="782" y="212">INTEGRITY</text>
      <line class="divider" x1="948" y1="155" x2="948" y2="237"/>
      <text class="value-text" x="980" y="175">
        <tspan x="980">We operate with honesty,</tspan>
        <tspan x="980" dy="25">transparency, and ethical standards</tspan>
        <tspan x="980" dy="25">in all aspects of our business.</tspan>
      </text>
    </g>

    <!-- Growth -->
    <g class="value-row row-red" transform="translate(0,564)">
      <use href="#value-block"/>
      <g class="icon" transform="translate(513,134)">
        <rect x="-26" y="0" width="10" height="18"/>
        <rect x="-10" y="-8" width="10" height="26"/>
        <rect x="6" y="-16" width="10" height="34"/>
        <path d="M-30,22 L28,22"/>
        <path d="M-28,-10 L-4,-24 L8,-20 L30,-40"/>
        <path d="M20,-40 L30,-40 L30,-30"/>
      </g>
      <text class="value-title" x="782" y="212">GROWTH</text>
      <line class="divider" x1="948" y1="155" x2="948" y2="237"/>
      <text class="value-text" x="980" y="162">
        <tspan x="980">We are committed to continuous</tspan>
        <tspan x="980" dy="25">improvement—of our people,</tspan>
        <tspan x="980" dy="25">our processes, and our impact</tspan>
        <tspan x="980" dy="25">in the industry.</tspan>
      </text>
    </g>

    <!-- Footer -->
    <polygon class="footer-band" points="0,1025 225,910 1450,910 1450,1025"/>
    <g class="contact">
      <g class="contact-icon" transform="translate(242,962)">
        <circle cx="0" cy="0" r="15"/>
        <path d="M-6,-8 L-3,-8 L-1,-3 L-3,-1 C-2,2 1,5 4,6 L6,4 L10,6 L10,9 C3,10 -8,0 -6,-8 Z"/>
      </g>
      <text class="contact-text" x="273" y="975">555.014.2290</text>

      <g class="contact-icon" transform="translate(518,962)">
        <rect x="-17" y="-11" width="34" height="22"/>
        <path d="M-17,-11 L0,3 L17,-11"/>
      </g>
      <text class="contact-text" x="550" y="975">hello@brovick.com</text>

      <g class="contact-icon" transform="translate(853,962)">
        <circle cx="0" cy="0" r="14"/>
        <ellipse cx="0" cy="0" rx="6" ry="14"/>
        <path d="M-14,0 L14,0 M-12,-7 L12,-7 M-12,7 L12,7"/>
      </g>
      <text class="contact-text" x="883" y="975">www.brovick.com</text>
    </g>
  </svg>
</main>
</body>
</html>
```